Website redesign www.marigoldlawpc.com law firm site

Need to redesign the website that I currently have to look more modern and professional. Would also like to be able to make updates and post without having a huge hassle. See current www.marigoldlawpc.com. I just think that it looks very immature and it's very templated there's no ability for me to make posts or Add links or anything like that

Target Market(s)

California people looking for a powerhouse attorney in

Industry/Entity Type

Legal

Number of Pages Required

3 page

Font styles to use
Serif
Sans Serif

Colors
ec1f27
000000
ffffff

Requirements
Must have
• Must be mobile friendly. Must look professional and have ability to post links to other websites. Must have ability to post blogs or articles. Would like to be able to read my FeeTrove account and also have the ability to upload forms for people to download
Nice to have
• Simple design easy to use and not cluttered with too much text

```html
<!DOCTYPE html>
<html lang="en">
<head>
<meta charset="utf-8">
<title>Marigold Law P.C.</title>
<link rel="stylesheet" href="https://fonts.googleapis.com/css2?family=Cinzel:wght@400;700&family=Roboto+Slab:wght@400;700&family=Roboto:ital,wght@0,400;0,500;0,700;1,400&display=swap">
<style>
:root{
  --red:#ec1f27;
  --red-deep:#b5121a;
  --black:#000;
  --ink:#222;
  --white:#fff;
  --muted:#555;
  --line:#dcdcdc;
  --footer:#2a2a2a;
  --footer-base:#1b1b1b;
  --footer-text:#cfcfcf;
}
*{box-sizing:border-box;margin:0;padding:0}
html,body{width:1200px;height:3644px;overflow:hidden}
body{font-family:"Roboto",sans-serif;color:var(--ink);background:var(--white);position:relative}
section,header,nav,footer{position:relative;width:1200px}
.abs{position:absolute}
.heading{font-family:"Roboto Slab",serif;font-weight:400;font-size:32px;color:var(--ink);text-align:center;width:100%}
.heading em{font-style:normal;color:var(--red)}

/* header */
.site-header{height:114px;background:var(--white)}
.brand{left:126px;top:22px;font-family:"Cinzel",serif;font-weight:700;font-size:38px;color:var(--red);letter-spacing:1px}
.contact-chip{top:36px;display:flex;align-items:center;gap:10px;font-size:15px;color:var(--ink)}
.chip-icon{width:32px;height:32px;border-radius:50%;background:var(--red);display:flex;align-items:center;justify-content:center}

/* nav */
.main-nav{height:44px;background:var(--black);display:flex;align-items:stretch;padding-left:100px}
.main-nav a{font-family:"Cinzel",serif;font-weight:700;font-size:14px;color:var(--white);text-decoration:none;display:flex;align-items:center;padding:0 30px}
.main-nav a.active{background:var(--red);padding:0 38px}
.main-nav a + a{margin-left:6px}

/* hero */
.hero{height:515px;background:linear-gradient(120deg,#2a1a10 0%,#6b3f22 40%,#a9713d 60%,#3a2414 100%)}
.hero-caption{left:0;top:440px;width:1200px;text-align:center;font-family:"Cinzel",serif;font-weight:700;font-size:23px;line-height:38px;color:var(--white);text-shadow:0 2px 4px rgba(0,0,0,.7)}
.hero-arrow{top:390px;width:30px;height:30px;background:rgba(0,0,0,.7);display:flex;align-items:center;justify-content:center}

/* welcome */
.welcome{height:554px}
.welcome .heading{top:26px;left:0}
.welcome-text{left:100px;top:100px;width:1000px;text-align:center;font-size:14px;line-height:24px;color:var(--muted)}
.btn-more{left:532px;top:201px;width:136px;height:34px;background:#2b2b2b;color:var(--white);font-family:"Roboto Slab",serif;font-size:15px;display:flex;align-items:center;justify-content:center}
.pillar{top:288px;width:260px;text-align:center}
.pillar h3{font-family:"Roboto Slab",serif;font-weight:400;font-size:24px;margin-bottom:14px}
.pillar-icon{width:86px;height:86px;border-radius:50%;background:var(--red);margin:0 auto 20px;display:flex;align-items:center;justify-content:center}
.pillar p{font-size:13px;line-height:18px;color:var(--muted)}

/* practice areas */
.practice{height:553px;background:linear-gradient(135deg,var(--red-deep) 0%,var(--red) 50%,var(--red-deep) 100%)}
.practice .heading{color:var(--white);top:30px;left:0}
.area{width:230px;color:var(--white)}
.area h3{font-family:"Roboto Slab",serif;font-weight:700;font-size:16px;margin-bottom:2px}
.area p{font-size:12px;line-height:15px}
.area.right-align{text-align:right}
.area.center{text-align:center}
.practice-name{left:0;top:398px;width:1200px;text-align:center;font-family:"Cinzel",serif;font-size:30px;color:var(--white)}

/* blog */
.blog{height:571px}
.blog .heading{top:50px;left:0}
.post{top:163px;width:473px}
.post-date{width:48px;height:48px;background:var(--red);color:var(--white);text-align:center;font-size:13px;font-weight:700;line-height:18px;padding-top:6px;position:absolute;left:0;top:0}
.post-date sup{font-size:8px}
.post-title{position:absolute;left:62px;top:0;font-size:16px;line-height:22px;font-weight:500}
.post-image{position:absolute;left:0;top:68px;width:473px;height:170px}
.post-text{position:absolute;left:0;top:255px;font-size:13px;line-height:17px;color:var(--muted)}
.dots{left:0;top:500px;width:1200px;display:flex;justify-content:center;gap:8px}
.dots span{width:8px;height:8px;border-radius:50%;background:#ccc}
.dots span.on{background:var(--red)}

/* testimonials */
.testimonials{height:386px;background:linear-gradient(135deg,var(--red-deep) 0%,var(--red) 50%,var(--red-deep) 100%)}
.testimonials .heading{color:var(--white);top:40px;left:0}
.portrait{top:111px;width:114px;height:114px;border-radius:50%;border:4px solid var(--white);background:radial-gradient(circle at 50% 40%,#c9ccd1,#6f7780)}
.quote{top:222px;width:320px;color:var(--white)}
.quote-mark{position:absolute;left:0;top:-14px;font-family:"Roboto Slab",serif;font-size:90px;line-height:90px;color:rgba(255,255,255,.85)}
.quote p{padding-left:60px;font-style:italic;font-size:13px;line-height:17px;text-align:center}
.quote .who{padding-left:60px;margin-top:38px;text-align:center;font-size:14px;font-weight:700}
.slide-arrow{top:181px;width:36px;height:36px;border-radius:50%;background:#222;display:flex;align-items:center;justify-content:center}

/* ratings */
.ratings{height:401px}
.ratings .heading{top:44px;left:0}
.ratings-sub{left:0;top:126px;width:1200px;text-align:center;font-size:13px;color:var(--ink)}
.badge{top:192px;width:278px;height:115px;border:1px solid var(--line);display:flex;align-items:center;justify-content:center}

/* newsletter */
.newsletter{height:144px;background:var(--red)}
.newsletter-title{left:185px;top:40px;font-family:"Roboto Slab",serif;font-size:24px;color:var(--white)}
.newsletter-text{left:185px;top:78px;width:390px;font-size:12px;line-height:15px;color:rgba(255,255,255,.9)}
.email-field{left:593px;top:39px;width:374px;height:46px;background:var(--white);font-size:12px;color:#888;display:flex;align-items:center;padding-left:14px}
.btn-subscribe{left:981px;top:39px;width:124px;height:46px;background:var(--black);color:var(--white);font-size:12px;font-weight:700;display:flex;align-items:center;justify-content:center;letter-spacing:.5px}

/* footer */
.site-footer{height:318px;background:var(--footer);color:var(--footer-text)}
.footer-head{top:42px;font-family:"Roboto Slab",serif;font-size:18px;color:var(--white)}
.footer-head em{font-style:normal;color:var(--red)}
.quick-links{left:100px;top:82px;list-style:none;font-size:12px;line-height:29px}
.quick-links li::before{content:"• ";color:var(--footer-text)}
.quick-links li.active{color:var(--red)}
.contact-list{left:301px;top:82px;font-size:12px;line-height:17px}
.contact-row{display:flex;align-items:center;gap:8px;margin-top:12px}
.map{left:554px;top:80px;width:257px;height:168px;background:linear-gradient(135deg,#ecebe6,#d9d6cc)}
.pay-box{left:850px;top:95px;width:243px;height:131px;background:var(--white);border:2px solid #1d3a6b;text-align:center}
.pay-box .tag{margin-top:10px;font-size:11px;color:#1d3a6b;font-weight:500}
.pay-box .pay-name{margin-top:12px;font-family:"Roboto Slab",serif;font-size:40px;color:#1d3a6b}
.pay-box .rule{margin:10px auto 0;width:190px;height:2px;background:#1d3a6b}
.footer-base{height:44px;background:var(--footer-base);color:#aaa;font-size:12px}
.copyright{left:100px;top:14px}
.social{top:9px;width:26px;height:26px;border-radius:50%}
</style>
</head>
<body>

<header class="site-header">
  <div class="abs brand">Marigold Law P.C.</div>
  <div class="abs contact-chip" style="left:656px">
    <span class="chip-icon"><svg width="16" height="16" viewBox="0 0 24 24"><path fill="#fff" d="M6.6 10.8a15.1 15.1 0 0 0 6.6 6.6l2.2-2.2a1 1 0 0 1 1-.25 11.4 11.4 0 0 0 3.6.57 1 1 0 0 1 1 1V20a1 1 0 0 1-1 1A17 17 0 0 1 3 4a1 1 0 0 1 1-1h3.5a1 1 0 0 1 1 1c0 1.25.2 2.45.57 3.57a1 1 0 0 1-.25 1z"/></svg></span>
    (530) 555-0148
  </div>
  <div class="abs contact-chip" style="left:840px">
    <span class="chip-icon"><svg width="16" height="16" viewBox="0 0 24 24"><path fill="#fff" d="M3 5h18v14H3z"/><path fill="none" stroke="#ec1f27" stroke-width="2" d="M3 6l9 7 9-7"/></svg></span>
    dana@marigoldlawgroup.com
  </div>
</header>

<nav class="main-nav">
  <a class="active">Home</a>
  <a>Attorney Profile</a>
  <a>Practice Areas &#9662;</a>
  <a>Client Reviews</a>
  <a>Links</a>
  <a>Contact Us</a>
</nav>

<section class="hero" role="img" aria-label="Judge's gavel resting beside an open law book on a wooden desk">
  <div class="abs hero-arrow" style="left:0"><svg width="10" height="12" viewBox="0 0 10 12"><path d="M8 1L2 6l6 5" fill="none" stroke="#fff" stroke-width="2"/></svg></div>
  <div class="abs hero-arrow" style="right:0"><svg width="10" height="12" viewBox="0 0 10 12"><path d="M2 1l6 5-6 5" fill="none" stroke="#fff" stroke-width="2"/></svg></div>
  <p class="abs hero-caption">A Boutique Law Firm Opportunity For Clients Who Want To Enjoy All The<br>Advantages Of Dana's Broad Legal Experience And Education.</p>
</section>

<section class="welcome">
  <h2 class="abs heading">Welcome to <em>Marigold Law P.C</em></h2>
  <p class="abs welcome-text">Marigold Law P.C. is owned by Dana L. Marlowe, a dedicated and caring professional who uses her broad range of skills as a California lawyer to bring consumers and business owners exceptionally strong legal representation that achieves best results. She works with people from across the northern region of California, from the Northern border to the Central Valley region.</p>
  <div class="abs btn-more">Read More</div>

  <div class="abs pillar" style="left:166px">
    <h3>Mission</h3>
    <div class="pillar-icon"><svg width="46" height="46" viewBox="0 0 46 46"><circle cx="23" cy="23" r="18" fill="none" stroke="#fff" stroke-width="4"/><circle cx="23" cy="23" r="10" fill="none" stroke="#fff" stroke-width="4"/><circle cx="23" cy="23" r="3" fill="#fff"/><path d="M23 23L40 6" stroke="#fff" stroke-width="3"/></svg></div>
    <p>Sed ut perspiciatis unde omnis iste natus error sit voluptatem accusantium doloremque laudantium,</p>
  </div>
  <div class="abs pillar" style="left:470px">
    <h3>Vision</h3>
    <div class="pillar-icon"><svg width="50" height="34" viewBox="0 0 50 34"><path d="M2 17C10 4 40 4 48 17 40 30 10 30 2 17z" fill="#fff"/><circle cx="25" cy="17" r="8" fill="#ec1f27"/><circle cx="25" cy="17" r="3.5" fill="#fff"/></svg></div>
    <p>Sed ut perspiciatis unde omnis iste natus error sit voluptatem accusantium doloremque laudantium,</p>
  </div>
  <div class="abs pillar" style="left:769px">
    <h3>Values</h3>
    <div class="pillar-icon"><svg width="44" height="40" viewBox="0 0 44 40"><rect x="4" y="26" width="7" height="12" fill="#fff"/><rect x="14" y="20" width="7" height="18" fill="#fff"/><rect x="24" y="14" width="7" height="24" fill="#fff"/><rect x="34" y="8" width="7" height="30" fill="#fff"/><path d="M4 20L16 10l8 5L38 2" fill="none" stroke="#fff" stroke-width="3"/></svg></div>
    <p>Sed ut perspiciatis unde omnis iste natus error sit voluptatem accusantium doloremque laudantium,</p>
  </div>
</section>

<section class="practice">
  <h2 class="abs heading">Practice Areas</h2>
  <svg class="abs" style="left:0;top:0" width="1200" height="553" viewBox="0 0 1200 553">
    <path d="M325 481A275 275 0 0 1 875 481" fill="none" stroke="#fff" stroke-width="5"/>
    <line x1="460" y1="455" x2="740" y2="455" stroke="#fff" stroke-width="2"/>
    <g fill="#fff">
      <circle cx="325" cy="481" r="36"/><circle cx="362" cy="343" r="36"/><circle cx="462" cy="243" r="36"/>
      <circle cx="600" cy="206" r="36"/><circle cx="738" cy="243" r="36"/><circle cx="838" cy="343" r="36"/><circle cx="875" cy="481" r="36"/>
    </g>
    <g fill="#ec1f27">
      <!-- business -->
      <rect x="309" y="470" width="32" height="22" rx="2"/><rect x="318" y="464" width="14" height="6" fill="none" stroke="#ec1f27" stroke-width="3"/>
      <!-- real estate -->
      <path d="M346 345l16-14 16 14h-4v14h-24v-14z"/>
      <!-- bankruptcy -->
      <circle cx="462" cy="243" r="16"/>
      <text x="462" y="251" text-anchor="middle" font-family="Roboto,sans-serif" font-weight="700" font-size="22" fill="#fff">$</text>
      <!-- family -->
      <circle cx="590" cy="196" r="5"/><circle cx="610" cy="196" r="5"/><circle cx="600" cy="203" r="4"/>
      <path d="M582 220v-12a8 8 0 0 1 16 0v12zM602 220v-12a8 8 0 0 1 16 0v12z"/>
      <!-- criminal -->
      <circle cx="729" cy="246" r="8" fill="none" stroke="#ec1f27" stroke-width="4"/><circle cx="747" cy="246" r="8" fill="none" stroke="#ec1f27" stroke-width="4"/>
      <!-- civil -->
      <path d="M821 350a17 17 0 0 1 34 0h4v5h-42v-5z"/>
      <!-- unlawful detainer -->
      <rect x="864" y="465" width="24" height="10" rx="2" transform="rotate(-35 876 470)"/><rect x="864" y="478" width="5" height="18" transform="rotate(45 866 487)"/><rect x="862" y="494" width="26" height="4"/>
    </g>
  </svg>
  <div class="abs area center" style="left:485px;top:119px"><h3>Family Law</h3><p>Sed ut perspiciatis unde omnis<br>sit voluptatem accusantium</p></div>
  <div class="abs area right-align" style="left:170px;top:205px"><h3>Bankruptcy</h3><p>Sed ut perspiciatis unde omnis<br>sit voluptatem accusantium</p></div>
  <div class="abs area right-align" style="left:80px;top:315px"><h3>Real Estate Law</h3><p>Sed ut perspiciatis unde omnis<br>sit voluptatem accusantium</p></div>
  <div class="abs area right-align" style="left:50px;top:455px"><h3>Business Law</h3><p>Sed ut perspiciatis unde omnis<br>sit voluptatem accusantium</p></div>
  <div class="abs area" style="left:800px;top:205px"><h3>Criminal Law</h3><p>Sed ut perspiciatis unde omnis<br>sit voluptatem accusantium</p></div>
  <div class="abs area" style="left:884px;top:315px"><h3>Civil Litigation</h3><p>Sed ut perspiciatis unde omnis<br>sit voluptatem accusantium</p></div>
  <div class="abs area" style="left:925px;top:448px"><h3>Unlawful Detainer</h3><p>Sed ut perspiciatis unde omnis<br>sit voluptatem accusantium</p></div>
  <div class="abs practice-name">Marigold Law P.C.</div>
</section>

<section class="blog">
  <h2 class="abs heading">Latest From <em>Our Blog</em></h2>
  <article class="abs post" style="left:100px">
    <div class="post-date">17<sup>th</sup><br>Feb</div>
    <h3 class="post-title">Lorem ipsum dolor sit amet, consectetuer<br>adipiscing elit doloremque.</h3>
    <div class="post-image" role="img" aria-label="Gavel resting on a historic constitution document" style="background:linear-gradient(135deg,#d9c7a2,#8a6a3e 60%,#3b2a18)"></div>
    <p class="post-text">Fusce elementum, nulla vel pellentes consequat, ante nulla hendrerit arcu, ac tincidunt mauris lacus sed leo. vamus suscipit molestie vestibulum. Lorem ipsum dolor sit amet,</p>
  </article>
  <article class="abs post" style="left:629px">
    <div class="post-date">17<sup>th</sup><br>Feb</div>
    <h3 class="post-title">Lorem ipsum dolor sit amet, consectetuer<br>adipiscing elit doloremque.</h3>
    <div class="post-image" role="img" aria-label="Brass scales of justice in a wood-panelled courtroom" style="background:linear-gradient(135deg,#5a2e1a,#9a5a32 50%,#3a1e10)"></div>
    <p class="post-text">Fusce elementum, nulla vel pellentes consequat, ante nulla hendrerit arcu, ac tincidunt mauris lacus sed leo. vamus suscipit molestie vestibulum. Lorem ipsum dolor sit amet,</p>
  </article>
  <div class="abs dots"><span class="on"></span><span></span><span></span><span></span></div>
</section>

<section class="testimonials">
  <h2 class="abs heading">What Peoples Say</h2>
  <div class="abs slide-arrow" style="left:60px"><svg width="10" height="12" viewBox="0 0 10 12"><path d="M8 1L2 6l6 5" fill="none" stroke="#fff" stroke-width="2"/></svg></div>
  <div class="abs slide-arrow" style="left:1102px"><svg width="10" height="12" viewBox="0 0 10 12"><path d="M2 1l6 5-6 5" fill="none" stroke="#fff" stroke-width="2"/></svg></div>

  <div class="abs portrait" style="left:208px" role="img" aria-label="Client portrait"></div>
  <div class="abs portrait" style="left:543px" role="img" aria-label="Client portrait"></div>
  <div class="abs portrait" style="left:881px" role="img" aria-label="Client portrait"></div>

  <div class="abs quote" style="left:114px"><span class="quote-mark">&ldquo;</span><p>Lorem ipsum dolor sit amet, consectetuer adipiscing elit, sed diam nonummy Lorem ipsum dolor sit amet, consectetuer adipiscing elit,</p><div class="who">- Consectetue Radipiscing</div></div>
  <div class="abs quote" style="left:449px"><span class="quote-mark">&ldquo;</span><p>Lorem ipsum dolor sit amet, consectetuer adipiscing elit, sed diam nonummy Lorem ipsum dolor sit amet, consectetuer adipiscing elit,</p><div class="who">- Diam Nonummy</div></div>
  <div class="abs quote" style="left:787px"><span class="quote-mark">&ldquo;</span><p>Lorem ipsum dolor sit amet, consectetuer adipiscing elit, sed diam nonummy Lorem ipsum dolor sit amet, consectetuer adipiscing elit,</p><div class="who">- Dolor Sitamet</div></div>
</section>

<section class="ratings">
  <h2 class="abs heading">Ratings and <em>Reviews</em></h2>
  <p class="abs ratings-sub">Lawyer Dana L. Marlowe, Esq. &nbsp;&nbsp;|&nbsp;&nbsp; Featured Attorney Bankruptcy / Chapter 7</p>
  <div class="abs badge" style="left:136px"><svg width="80" height="80" viewBox="0 0 80 80"><circle cx="40" cy="40" r="36" fill="none" stroke="#1d5aa8" stroke-width="4"/></svg></div>
  <div class="abs badge" style="left:461px"><svg width="86" height="86" viewBox="0 0 86 86"><circle cx="43" cy="43" r="40" fill="none" stroke="#555" stroke-width="2"/><circle cx="43" cy="43" r="30" fill="none" stroke="#555" stroke-width="1.5"/></svg></div>
  <div class="abs badge" style="left:785px"><svg width="200" height="30" viewBox="0 0 200 30"><rect width="200" height="30" fill="#2d5a8c" opacity=".85"/></svg></div>
</section>

<section class="newsletter">
  <svg class="abs" style="left:100px;top:52px" width="60" height="42" viewBox="0 0 60 42"><rect x="2" y="2" width="56" height="38" fill="none" stroke="#fff" stroke-width="3"/><path d="M2 2l28 22L58 2M2 40l20-18M58 40L38 22" fill="none" stroke="#fff" stroke-width="3"/></svg>
  <h2 class="abs newsletter-title">Subscribe To Our Newsletter</h2>
  <p class="abs newsletter-text">Aenean tortor adipiscing elit, sed diam nonummy nibh euismod tincidunt in vulputate velit esse molestie...</p>
  <div class="abs email-field">Enter Your Email Here</div>
  <div class="abs btn-subscribe">SUBSCRIBE</div>
</section>

<footer class="site-footer">
  <h3 class="abs footer-head" style="left:100px">Quick <em>Links</em></h3>
  <ul class="abs quick-links">
    <li class="active">Home</li><li>Attorney Profile</li><li>Practice Areas</li><li>Client Reviews</li><li>Links</li><li>Blog</li><li>Contact Us</li>
  </ul>
  <h3 class="abs footer-head" style="left:301px">Contact <em>Details</em></h3>
  <div class="abs contact-list">
    <p>Marigold Law P.C<br>48 Orchard Avenue<br>Suite 200, Chico, CA 95928</p>
    <div class="contact-row"><svg width="12" height="12" viewBox="0 0 24 24"><path fill="#cfcfcf" d="M6.6 10.8a15.1 15.1 0 0 0 6.6 6.6l2.2-2.2a1 1 0 0 1 1-.25 11.4 11.4 0 0 0 3.6.57 1 1 0 0 1 1 1V20a1 1 0 0 1-1 1A17 17 0 0 1 3 4a1 1 0 0 1 1-1h3.5a1 1 0 0 1 1 1c0 1.25.2 2.45.57 3.57a1 1 0 0 1-.25 1z"/></svg>(530) 555-0148</div>
    <div class="contact-row"><svg width="12" height="12" viewBox="0 0 24 24"><rect x="6" y="2" width="12" height="20" rx="2" fill="none" stroke="#cfcfcf" stroke-width="2"/></svg>(888) 555-0172</div>
    <div class="contact-row"><svg width="12" height="12" viewBox="0 0 24 24"><path fill="#cfcfcf" d="M2 5h20v14H2z"/><path fill="none" stroke="#2a2a2a" stroke-width="2" d="M2 6l10 7 10-7"/></svg>dana@marigoldlawgroup.com</div>
  </div>
  <h3 class="abs footer-head" style="left:554px">Location <em>Map</em></h3>
  <div class="abs map" role="img" aria-label="Street map of downtown Chico with the office location pinned">
    <svg class="abs" style="left:112px;top:50px" width="30" height="40" viewBox="0 0 30 40"><path d="M15 0C7 0 1 6 1 14c0 10 14 26 14 26s14-16 14-26C29 6 23 0 15 0z" fill="#ec1f27"/><circle cx="15" cy="14" r="5" fill="#fff"/></svg>
  </div>
  <div class="abs pay-box">
    <div class="tag">Make Secure Online Payment</div>
    <div class="pay-name">FeeTrove</div>
    <div class="rule"></div>
  </div>
</footer>

<div class="footer-base" style="position:relative;width:1200px">
  <p class="abs copyright">&copy; 2016 Marigold Law P.C . All Rights Reserved.</p>
  <span class="abs social" style="left:992px;background:#3b5998"></span>
  <span class="abs social" style="left:1030px;background:#0e76a8"></span>
  <span class="abs social" style="left:1068px;background:#1da1f2"></span>
</div>

</body>
</html>
```